Garlic Farm for Farm Sales/Restaurant sales

Need a professional, but appealing to agriculture world. We are selling 27 kinds of Organic Garlic from a farm in Simla,CO. I have uploaded logo and business information-we are going to need a template, because I will need to use it for four separate people.
-We are trying to appeal to Farm to table restaurants
-As well as growers/farmers

Target Market(s)

Agriculture Sales/Restaurants-Organic

Industry/Entity Type

Agriculture

Contact Information for Business Card

Want it to look more unique then your average kelto stock card- I want it to look amazing

Font styles to use
Sans Serif

Colors
0455a3
ec1f27
fbed22
ffffff

Requirements
Must have
• Just be creative
Nice to have
• Colorful
Should not have
• plain

```html
<!DOCTYPE html>
<html lang="en">
<head>
<meta charset="utf-8">
<title>Prairie Clove Garlic – Business Card</title>
<link href="https://fonts.googleapis.com/css2?family=Open+Sans:wght@400;600;700&display=swap" rel="stylesheet">
<style>
  :root {
    --navy: #0d3466;
    --brand-blue: #0455a3;
    --red: #d7283a;
    --yellow: #fbd822;
    --white: #ffffff;
    --ink: #3b3f46;
    --rule: #cfd3d9;
    --backdrop: #e9e6e1;
  }
  * { box-sizing: border-box; margin: 0; padding: 0; }
  html, body { width: 1200px; height: 950px; overflow: hidden; }
  body {
    background: var(--backdrop);
    font-family: "Open Sans", Arial, sans-serif;
    position: relative;
  }
  .card {
    position: absolute;
    left: 250px;
    width: 700px;
    height: 400px;
    border-radius: 26px;
    overflow: hidden;
    box-shadow: 0 6px 18px rgba(0,0,0,0.18);
  }
  .card-front { top: 50px; background: var(--white); }
  .card-back { top: 500px; background: var(--navy); }

  .front-wave { position: absolute; inset: 0; width: 700px; height: 400px; }

  .brand {
    position: absolute;
    display: flex;
    align-items: center;
    gap: 14px;
    color: var(--navy);
    font-weight: 700;
  }
  .brand-dot { border-radius: 50%; background: var(--red); flex: none; }
  .brand-front { left: 56px; top: 150px; font-size: 30px; line-height: 1.05; }
  .brand-front .brand-dot { width: 58px; height: 58px; }

  .identity { position: absolute; left: 395px; top: 50px; }
  .person-name { font-size: 24px; font-weight: 600; color: var(--navy); letter-spacing: 0.5px; }
  .person-title { font-size: 17px; font-weight: 600; color: var(--red); margin-top: 2px; }
  .address { font-size: 15px; color: var(--ink); margin-top: 10px; line-height: 1.45; }

  .divider { position: absolute; left: 320px; top: 182px; width: 310px; height: 1px; background: var(--rule); }

  .contacts { position: absolute; left: 395px; top: 200px; list-style: none; }
  .contacts li {
    display: flex; align-items: center; gap: 10px;
    font-size: 15px; color: var(--ink); line-height: 1.6;
  }
  .contacts svg { width: 14px; height: 14px; fill: var(--navy); flex: none; }

  .social-rule { position: absolute; left: 95px; top: 40px; width: 1px; height: 320px; background: rgba(255,255,255,0.55); }
  .social-list { position: absolute; left: 80px; top: 128px; list-style: none; }
  .social-list li {
    width: 30px; height: 30px; border-radius: 50%;
    border: 1.5px solid var(--white); background: var(--navy);
    margin-bottom: 10px;
  }
  .brand-back { left: 250px; top: 160px; font-size: 38px; color: var(--white); line-height: 1.05; }
  .brand-back .brand-dot { width: 80px; height: 80px; }
</style>
</head>
<body>

<section class="card card-front" aria-label="Business card front">
  <svg class="front-wave" viewBox="0 0 700 400" aria-hidden="true">
    <path d="M0,300 C220,300 470,330 700,228" fill="none" stroke="var(--yellow)" stroke-width="7"/>
    <path d="M0,313 C220,313 470,343 700,241" fill="none" stroke="var(--red)" stroke-width="6"/>
    <path d="M0,325 C220,325 470,355 700,253 L700,400 L0,400 Z" fill="var(--navy)"/>
  </svg>

  <div class="brand brand-front">
    <span class="brand-dot"></span>
    <span class="brand-name">Prairie Clove<br>Garlic</span>
  </div>

  <div class="identity">
    <p class="person-name">DANA WHITLOW</p>
    <p class="person-title">CEO/FOUNDER</p>
    <p class="address">P.O. Box 18 Elmvale<br>CO 80999</p>
  </div>

  <div class="divider"></div>

  <ul class="contacts">
    <li>
      <svg viewBox="0 0 24 24"><path d="M6.6 10.8a15.2 15.2 0 0 0 6.6 6.6l2.2-2.2a1 1 0 0 1 1-.25 11.4 11.4 0 0 0 3.6.57 1 1 0 0 1 1 1V20a1 1 0 0 1-1 1A17 17 0 0 1 3 4a1 1 0 0 1 1-1h3.5a1 1 0 0 1 1 1c0 1.25.2 2.45.57 3.57a1 1 0 0 1-.25 1z"/></svg>
      555-014-2290
    </li>
    <li>
      <svg viewBox="0 0 24 24"><path d="M2 5h20v14H2z M2 5l10 8 10-8" /></svg>
      Lena@PCGarlic.com
    </li>
    <li>
      <svg viewBox="0 0 24 24"><circle cx="12" cy="12" r="10"/></svg>
      www.PCGarlic.com
    </li>
  </ul>
</section>

<section class="card card-back" aria-label="Business card back">
  <div class="social-rule"></div>
  <ul class="social-list" aria-label="Social links">
    <li></li><li></li><li></li><li></li>
  </ul>
  <div class="brand brand-back">
    <span class="brand-dot"></span>
    <span class="brand-name">Prairie Clove<br>Garlic</span>
  </div>
</section>

</body>
</html>
```